Tandem Hearth Works Pty Ltd

We need business cards for a company based in Perth, we install, service and maintain fire equipment.
On the front we want a great design with our logo and a small spot for our full company name, general company email address and office number. On the back we need space for our name, title, mobile number and email address on the back.

Target Market(s)

Facility managers and commercial/industrial building owners/occupiers.

Contact Information for Business Card

Font styles to use
Sans Serif

Requirements
Must have
• Please only submit 5 of your best samples.
Darker tones are preferred.
Nice to have
• We want to use, black, red and grey. Keep it modern and clean.
I've attached the company logo and a sample of a boarder we use on our emergency plans.
Should not have
• No preference. Let the designer choose.

```html
<!DOCTYPE html>
<html lang="en">
<head>
<meta charset="utf-8">
<title>Tandem Hearth Works Pty Ltd — Business Cards</title>
<link rel="stylesheet" href="https://fonts.googleapis.com/css2?family=Poppins:wght@300;400;600;700;800&display=swap">
<style>
  :root {
    --backdrop: #1b1b1b;
    --card: #0c0c0c;
    --card-edge: #151515;
    --red: #e0202b;
    --white: #f2f2f2;
    --grey: #b9b9b9;
    --divider: #3a3a3a;
  }
  * { box-sizing: border-box; margin: 0; padding: 0; }
  html, body {
    width: 1200px; height: 900px; overflow: hidden;
    background: var(--backdrop);
    font-family: "Poppins", Arial, sans-serif;
  }
  .stage {
    position: relative; width: 1200px; height: 900px;
    display: flex; flex-direction: column; align-items: center; justify-content: center;
    gap: 60px;
  }
  .card {
    position: relative; width: 560px; height: 320px;
    background: var(--card);
    border-radius: 26px;
    box-shadow: 0 0 0 1px var(--card-edge);
    overflow: hidden;
  }

  /* Brand name */
  .brand-mark {
    position: absolute; display: flex; align-items: flex-start; gap: 12px;
    color: var(--red); font-weight: 800; text-transform: uppercase;
    line-height: 0.95; letter-spacing: 0.5px;
  }
  .brand-mark .square { width: 16px; height: 16px; background: var(--red); margin-top: 6px; flex: none; }

  /* Front */
  .card--front .brand-mark { left: 44px; top: 40px; font-size: 38px; }
  .front-bar {
    position: absolute; left: 44px; right: 0; top: 178px; height: 10px;
    background: var(--red);
  }
  .company-name {
    position: absolute; left: 290px; top: 110px;
    color: var(--white); font-size: 17px; line-height: 1.12; text-transform: uppercase;
    font-weight: 300; letter-spacing: 0.5px;
  }
  .company-name strong { font-weight: 700; display: block; }
  .contact {
    position: absolute; display: flex; align-items: center; gap: 10px;
    color: var(--grey); font-size: 14px; font-weight: 300; letter-spacing: 0.4px;
    white-space: nowrap;
  }
  .contact svg { width: 14px; height: 14px; fill: var(--red); flex: none; }
  .card--front .contact--phone { left: 60px; top: 226px; }
  .card--front .contact--email { left: 290px; top: 226px; }

  /* Back */
  .card--back .brand-mark { left: 44px; top: 110px; font-size: 30px; }
  .back-divider {
    position: absolute; left: 250px; top: 70px; width: 1px; height: 180px;
    background: var(--divider);
  }
  .person { position: absolute; left: 280px; top: 92px; }
  .person-name {
    color: var(--white); font-size: 19px; font-weight: 600; text-transform: uppercase; letter-spacing: 0.5px;
  }
  .person-title {
    color: var(--red); font-size: 11px; font-weight: 600; text-transform: uppercase; letter-spacing: 1px;
  }
  .person-rule { width: 56px; height: 1px; background: var(--red); margin-top: 10px; }
  .card--back .contact--phone { left: 280px; top: 180px; font-size: 13px; }
  .card--back .contact--email { left: 280px; top: 208px; font-size: 13px; }
</style>
</head>
<body>
<main class="stage">

  <section class="card card--front" aria-label="Business card front">
    <div class="brand-mark"><span class="square"></span><span>Tandem<br>Hearth<br>Works</span></div>
    <p class="company-name"><strong>Tandem</strong>Hearth Works<br>Pty Ltd</p>
    <div class="front-bar"></div>
    <p class="contact contact--phone">
      <svg viewBox="0 0 24 24" aria-hidden="true"><path d="M6.6 10.8a15.1 15.1 0 0 0 6.6 6.6l2.2-2.2a1 1 0 0 1 1-.25 11.4 11.4 0 0 0 3.6.57 1 1 0 0 1 1 1V20a1 1 0 0 1-1 1A17 17 0 0 1 3 4a1 1 0 0 1 1-1h3.5a1 1 0 0 1 1 1c0 1.25.2 2.45.57 3.57a1 1 0 0 1-.25 1z"/></svg>
      000 000 0000
    </p>
    <p class="contact contact--email">
      <svg viewBox="0 0 24 24" aria-hidden="true"><path d="M2 5h20v14H2z M2 5l10 8 10-8" /></svg>
      office@tandemhearth.com.au
    </p>
  </section>

  <section class="card card--back" aria-label="Business card back">
    <div class="brand-mark"><span class="square"></span><span>Tandem<br>Hearth<br>Works</span></div>
    <div class="back-divider"></div>
    <div class="person">
      <p class="person-name">Your Name</p>
      <p class="person-title">Job Title</p>
      <div class="person-rule"></div>
    </div>
    <p class="contact contact--phone">
      <svg viewBox="0 0 24 24" aria-hidden="true"><path d="M6.6 10.8a15.1 15.1 0 0 0 6.6 6.6l2.2-2.2a1 1 0 0 1 1-.25 11.4 11.4 0 0 0 3.6.57 1 1 0 0 1 1 1V20a1 1 0 0 1-1 1A17 17 0 0 1 3 4a1 1 0 0 1 1-1h3.5a1 1 0 0 1 1 1c0 1.25.2 2.45.57 3.57a1 1 0 0 1-.25 1z"/></svg>
      000 000 0000
    </p>
    <p class="contact contact--email">
      <svg viewBox="0 0 24 24" aria-hidden="true"><path d="M2 5h20v14H2z M2 5l10 8 10-8" /></svg>
      name@tandemhearth.com.au
    </p>
  </section>

</main>
</body>
</html>
```